Basic business card

use my newly created logo - and the phrases (Lower Cost of Test & Accelarated New Product Introduction) - and my new email domain / ID - use at conferences / tradeshows

Industry/Entity Type

semiconductor

Contact Information for Business Card

Daniel K Forde, Owner, communicate via Logo - Lower COT - Cost of Test, Accelerated NPI - New Product Introduction, phone +1 555 613 0946, Chandler, Arizona, USA, daniel.forde@qal-vub.com

Font styles to use
Sans Serif

Requirements
Nice to have
• re-use my logo created via Pixel Harbor last August (#7315926)

```html
<!DOCTYPE html>
<html lang="en">
<head>
<meta charset="utf-8">
<title>QAL-VUB Business Card</title>
<link rel="stylesheet" href="https://fonts.googleapis.com/css2?family=Open+Sans:wght@400;600;700&display=swap">
<style>
  :root {
    --backdrop: #232323;
    --card: #1d1d20;
    --card-pattern-a: #1a1a1c;
    --card-pattern-b: #26262a;
    --slate: #4b5468;
    --silver: #aeb7c6;
    --orange: #ee9220;
    --green: #78bd40;
    --white: #f2f2f2;
    --rule: #8a8a8a;
  }
  * { box-sizing: border-box; margin: 0; padding: 0; }
  html, body {
    width: 1200px; height: 780px; overflow: hidden;
    background: var(--backdrop);
    font-family: "Open Sans", Arial, sans-serif;
  }
  .stage { position: relative; width: 1200px; height: 780px; }
  .card {
    position: absolute; top: 241px;
    width: 520px; height: 297px;
    background: var(--card);
    overflow: hidden;
    box-shadow: 0 18px 40px rgba(0,0,0,.45);
  }
  .card--front { left: 50px; }
  .card--back { left: 630px; }

  /* front */
  .brand {
    position: absolute; left: 34px; top: 46px;
    font-size: 38px; font-weight: 400; letter-spacing: 1px;
    color: var(--slate);
  }
  .divider {
    position: absolute; left: 262px; top: 96px;
    width: 1px; height: 122px; background: var(--rule);
  }
  .person { position: absolute; left: 284px; top: 104px; }
  .person__name { font-size: 24px; font-weight: 700; line-height: 1.1; }
  .person__first { color: var(--orange); }
  .person__last { color: var(--green); }
  .person__title { color: var(--white); font-size: 13px; margin-top: 2px; }
  .contacts { list-style: none; margin-top: 12px; }
  .contacts li {
    display: flex; align-items: center; gap: 8px;
    color: var(--white); font-size: 13px; line-height: 20px;
  }
  .contacts svg { width: 12px; height: 12px; flex: none; }
  .address-band {
    position: absolute; left: 0; bottom: 0;
    width: 410px; height: 30px; background: var(--green);
    color: var(--white); font-size: 12px;
    display: flex; align-items: center; padding-left: 34px;
  }
  .accent-block {
    position: absolute; right: 0; bottom: 0;
    width: 110px; height: 30px; background: var(--orange);
  }

  /* back */
  .pattern-field {
    position: absolute; inset: 0;
    background: radial-gradient(ellipse at 50% 50%, var(--card-pattern-b), var(--card-pattern-a) 75%);
  }
  .back-brand {
    position: absolute; inset: 0;
    display: flex; align-items: center; justify-content: center;
    font-size: 48px; font-weight: 400; letter-spacing: 2px;
    color: var(--silver);
  }
</style>
</head>
<body>
<main class="stage">
  <section class="card card--front" aria-label="Business card front">
    <div class="brand">QAL-VUB</div>
    <div class="divider"></div>
    <div class="person">
      <p class="person__name"><span class="person__first">Lena</span> <span class="person__last">Marovic</span></p>
      <p class="person__title">Managing Director</p>
      <ul class="contacts">
        <li>
          <svg viewBox="0 0 12 12" aria-hidden="true"><path fill="#ee9220" d="M2.5 1l2 2.2-1 1.2c.6 1.4 1.7 2.5 3.1 3.1l1.2-1 2.2 2-1.2 1.5C5 9.8 2.2 7 1 3.2z"/></svg>
          (555) 274-1180
        </li>
        <li>
          <svg viewBox="0 0 12 12" aria-hidden="true"><rect x="0.5" y="2" width="11" height="8" rx="1" fill="#ee9220"/><path d="M1 2.8l5 3.8 5-3.8" stroke="#1d1d20" stroke-width="1" fill="none"/></svg>
          info@qal-vub.com
        </li>
        <li>
          <svg viewBox="0 0 12 12" aria-hidden="true"><circle cx="6" cy="6" r="5.5" fill="#ee9220"/><path d="M0.5 6h11M6 0.5c-2.5 3-2.5 8 0 11M6 0.5c2.5 3 2.5 8 0 11" stroke="#1d1d20" stroke-width=".8" fill="none"/></svg>
          www.qal-vub.com
        </li>
      </ul>
    </div>
    <div class="address-band">418 Linden Ridge Rd. Suite 120 Chandler, AZ 85226</div>
    <div class="accent-block"></div>
  </section>

  <section class="card card--back" aria-label="Business card back">
    <div class="pattern-field" role="img" aria-label="Embossed repeating brand pattern across the card"></div>
    <div class="back-brand">QAL-VUB</div>
  </section>
</main>
</body>
</html>
```